Website Design for Employee Moral and Happiness Company

Looking for a clean website design that explains our features in a step by step manner so our visitors know exactly what our site does before logging in.

The site is called "Velrato". See logo design and video for a sample of style and an overview of what we do.

Target Market(s)

Business owners that are looking to retain employees.

Number of Pages Required

1 page

```html
<!DOCTYPE html>
<html lang="en">
<head>
<meta charset="utf-8">
<title>Velrato</title>
<link href="https://fonts.googleapis.com/css2?family=Bitter:wght@400;500;700&family=Nunito:wght@400;600;700&display=swap" rel="stylesheet">
<style>
:root{
  --orange:#e8531f;
  --orange-mid:#f26d3a;
  --orange-soft:#f58c5e;
  --ink:#222222;
  --text:#3a3a3a;
  --muted:#5a5a5a;
  --band:#f2f1f3;
  --footer:#262626;
  --white:#ffffff;
}
*{margin:0;padding:0;box-sizing:border-box}
html,body{width:1200px;height:3569px;overflow:hidden;background:var(--white)}
body{position:relative;font-family:'Nunito',sans-serif;color:var(--text)}
.abs{position:absolute}
h1,h2,h3,.serif{font-family:'Bitter',serif;font-weight:400;color:var(--ink)}
.btn{position:absolute;background:var(--orange);color:var(--white);font-family:'Bitter',serif;font-size:15px;letter-spacing:.5px;display:flex;align-items:center;justify-content:center}
.photo{position:absolute}
/* header */
.site-header{position:absolute;left:0;top:0;width:1200px;height:72px;background:var(--white)}
.brand{position:absolute;left:132px;top:6px;font-family:'Bitter',serif;font-weight:700;font-size:44px;color:var(--ink);letter-spacing:1px}
.nav a{position:absolute;top:19px;font-family:'Bitter',serif;font-size:16px;color:var(--ink);text-decoration:none;line-height:28px;white-space:nowrap}
.nav a.active{background:var(--orange);color:var(--white);padding:0 8px}
.social-dot{position:absolute;top:20px;width:28px;height:28px;border:1.5px solid var(--ink);border-radius:50%}
/* hero */
.hero-panel{position:absolute;left:858px;top:267px;width:342px;height:185px;background:rgba(30,30,30,.78)}
.hero-panel .small{position:absolute;left:26px;top:20px;font-family:'Bitter',serif;font-size:28px;color:var(--white)}
.hero-panel .big{position:absolute;left:26px;top:50px;font-family:'Bitter',serif;font-size:52px;color:var(--white);letter-spacing:1px}
.dot{position:absolute;top:560px;width:8px;height:8px;background:var(--white)}
/* section titles */
.title-center{position:absolute;left:0;width:1200px;text-align:center;font-size:30px}
.rule{position:absolute;width:48px;height:3px;background:var(--orange)}
.feature{position:absolute;width:200px;font-size:12.5px;line-height:16px;color:var(--muted)}
.feature h3{font-size:15px;color:var(--ink);margin-bottom:4px}
.body-copy{position:absolute;font-size:15px;line-height:22.5px;text-align:justify;color:var(--text)}
.sec-title{position:absolute;font-size:30px}
.point{position:absolute;left:735px;width:340px;font-size:12.5px;line-height:16px;color:var(--muted)}
.point h3{font-size:15px;color:var(--ink);margin-bottom:4px}
.point-icon{position:absolute;left:651px;width:68px;height:68px;border-radius:50%;background:var(--orange)}
/* blog */
.card{position:absolute;top:2773px;width:295px;height:392px;border:1px solid #dcdcdc;background:var(--white)}
.card .img{position:absolute;left:0;top:0;width:293px;height:175px}
.card h3{position:absolute;left:25px;top:196px;width:250px;font-size:15px;line-height:18px}
.card p{position:absolute;left:25px;top:245px;width:245px;font-size:12.5px;line-height:17px;color:var(--muted)}
.card .btn{left:27px;top:330px;width:82px;height:26px;font-size:10.5px}
/* footer */
.footer{position:absolute;left:0;top:3205px;width:1200px;height:364px}
.foot-brand{position:absolute;left:132px;top:3300px;font-family:'Bitter',serif;font-weight:700;font-size:72px;color:var(--white);letter-spacing:2px}
.foot-h{position:absolute;top:3272px;font-size:13px;font-weight:700;color:var(--white);letter-spacing:.6px}
.foot-menu{position:absolute;left:483px;top:3302px;font-size:12px;line-height:20px;color:var(--white);list-style:none}
.foot-item{position:absolute;font-size:11.5px;line-height:15px;color:var(--white)}
.foot-icon{position:absolute;width:24px;height:24px;border-radius:50%;background:var(--white)}
.copyright{position:absolute;left:0;top:3518px;width:1200px;text-align:center;font-size:10px;color:var(--white)}
</style>
</head>
<body>

<header class="site-header">
  <div class="brand">velrato</div>
  <nav class="nav">
    <a class="active" style="left:538px">Home</a>
    <a style="left:626px">About Us</a>
    <a style="left:733px">Services</a>
    <a style="left:831px">Blog</a>
    <a style="left:898px">Contact Us</a>
  </nav>
  <span class="social-dot" style="left:1004px"></span>
  <span class="social-dot" style="left:1038px"></span>
</header>

<!-- hero -->
<div class="photo" role="img" aria-label="Colleagues giving each other a high five around an office meeting table" style="left:0;top:72px;width:1200px;height:560px;background:linear-gradient(120deg,#9fb4b8 0%,#6f7f7a 35%,#3e4a4a 65%,#2b3434 100%)"></div>
<svg class="abs" style="left:0;top:580px" width="1200" height="60" viewBox="0 0 1200 60">
  <path d="M0 20 C300 65 800 45 1200 25 L1200 60 L0 60Z" fill="#e6e6e6"/>
  <path d="M0 28 C300 72 800 55 1200 38 L1200 60 L0 60Z" fill="#ffffff"/>
</svg>
<div class="hero-panel">
  <div class="small">WELCOME TO</div>
  <div class="big">VELRATO</div>
</div>
<div class="btn" style="left:887px;top:385px;width:114px;height:35px">READ MORE</div>
<span class="dot" style="left:563px"></span>
<span class="dot" style="left:579px"></span>
<span class="dot" style="left:595px;background:var(--orange)"></span>
<span class="dot" style="left:611px"></span>
<span class="dot" style="left:627px"></span>

<!-- features -->
<h2 class="title-center" style="top:672px">Features</h2>
<span class="rule" style="left:576px;top:719px"></span>
<p class="abs serif" style="left:455px;top:750px;width:290px;text-align:center;font-size:14.5px;line-height:22px;color:var(--text)">Lorem Ipsum is simply dummy text of the printing and typesetting industry Lorem Ipsum has been the industry's.</p>

<svg class="abs" style="left:240px;top:715px" width="720" height="380" viewBox="0 0 720 380">
  <path d="M100 20 C160 5 205 40 190 100 C180 145 130 160 80 150 C20 140 0 100 15 60 C28 30 60 28 100 20Z" fill="var(--orange)"/>
  <path d="M270 160 C320 150 345 190 335 240 C325 285 285 300 245 290 C200 278 175 250 180 210 C185 178 225 165 270 160Z" fill="var(--orange-mid)"/>
  <path d="M470 170 C520 160 570 190 565 240 C560 290 520 310 475 300 C430 290 405 260 410 220 C415 190 440 175 470 170Z" fill="var(--orange-mid)"/>
  <path d="M610 8 C660 5 695 45 690 90 C682 140 640 160 600 152 C555 143 525 110 532 70 C540 30 575 10 610 8Z" fill="var(--orange-soft)"/>
  <g fill="none" stroke="#fff" stroke-width="4" stroke-linecap="round" stroke-linejoin="round">
    <path d="M75 85 L95 105 L130 65"/>
    <path d="M235 250 L235 268 L253 268 M290 218 L262 246 L258 262 L274 258 L302 230Z M240 215 L270 215 M240 215 L240 240"/>
    <rect x="463" y="208" width="44" height="30" rx="3"/>
    <path d="M455 250 L515 250"/>
    <circle cx="612" cy="80" r="33"/>
    <path d="M598 90 L626 90"/>
  </g>
</svg>

<div class="feature" style="left:132px;top:878px"><h3>1. Lorem ipsum</h3>Lorem Ipsum is simply dummy text of the printing and typesett ing industry Lorem Ipsum has been the industry's.</div>
<div class="feature" style="left:880px;top:878px"><h3>4. Lorem ipsum</h3>Lorem Ipsum is simply dummy text of the printing and typesett ing industry Lorem Ipsum has been the industry's.</div>
<div class="feature" style="left:276px;top:1027px"><h3>2. Lorem ipsum</h3>Lorem Ipsum is simply dummy text of the printing and typesett ing industry Lorem Ipsum has been the industry's.</div>
<div class="feature" style="left:781px;top:1030px"><h3>3. Lorem ipsum</h3>Lorem Ipsum is simply dummy text of the printing and typesett ing industry Lorem Ipsum has been the industry's.</div>

<!-- about -->
<div class="abs" style="left:0;top:1180px;width:1200px;height:475px;background:var(--band)"></div>
<div class="photo" role="img" aria-label="Smiling team standing with arms crossed in a bright office" style="left:600px;top:1180px;width:600px;height:475px;background:linear-gradient(90deg,#e9ecef 0%,#aebccb 40%,#7f93a8 75%,#c7ced6 100%)"></div>
<svg class="abs" style="left:0;top:1620px" width="1200" height="45" viewBox="0 0 1200 45">
  <path d="M0 30 C400 5 800 8 1200 18 L1200 45 L0 45Z" fill="#ffffff"/>
</svg>
<h2 class="sec-title" style="left:132px;top:1222px">About Us</h2>
<span class="rule" style="left:132px;top:1268px"></span>
<p class="body-copy" style="left:132px;top:1303px;width:432px;font-size:14.6px">There are many variations of passages of Lorem Ipsum available, but the majority have suffered alteration in some form, by injected humour, or randomised words which don't look even slightly believable. If you are going to use a passage of Lorem Ipsum, you need to be sure there isn't anything embarrassing hidden in the middle of text. All the Lorem Ipsum generators on the Internet tend to repeat predefined chunks as necessary, making this the first true generator on the Internet. It uses a dictionary of over 200 Latin words.</p>
<div class="btn" style="left:131px;top:1540px;width:115px;height:37px">READ MORE</div>

<!-- feature split -->
<div class="photo" role="img" aria-label="Woman reading a tablet by a window at night" style="left:132px;top:1733px;width:478px;height:382px;border-bottom-right-radius:380px 382px;background:linear-gradient(135deg,#3d3a34 0%,#5e4a38 45%,#2a2826 100%)"></div>
<h2 class="sec-title" style="left:657px;top:1723px">Lorem Ipsum is simply</h2>
<p class="body-copy" style="left:657px;top:1800px;width:410px">There are many variations of passages of Lorem Ipsum available, but the majority have suffered alteration in some form, by injected humour, or randomised words which don't look even slightly believable.</p>
<span class="point-icon" style="top:1920px"></span>
<svg class="abs" style="left:665px;top:1934px" width="40" height="40" viewBox="0 0 40 40"><g fill="none" stroke="#fff" stroke-width="3"><circle cx="20" cy="17" r="10"/><path d="M13 25 L10 36 L16 33 L20 37 L24 33 L30 36 L27 25"/></g></svg>
<div class="point" style="top:1921px"><h3>Lorem ipsum</h3>Lorem Ipsum is simply dummy text of the printing and typesett ing industry Lorem Ipsum has been the industry's. dummy tyxt.</div>
<span class="point-icon" style="top:2032px"></span>
<svg class="abs" style="left:665px;top:2046px" width="40" height="40" viewBox="0 0 40 40"><g fill="#fff"><circle cx="20" cy="12" r="7"/><path d="M6 36 C6 24 34 24 34 36Z"/></g></svg>
<div class="point" style="top:2033px"><h3>Lorem ipsum</h3>Lorem Ipsum is simply dummy text of the printing and typesett ing industry Lorem Ipsum has been the industry's. dummy tyxt.</div>

<!-- hex section -->
<div class="abs" style="left:0;top:2225px;width:1200px;height:433px;background:var(--band)"></div>
<h2 class="sec-title" style="left:131px;top:2270px">Lorem Ipsum is simply</h2>
<span class="rule" style="left:131px;top:2316px"></span>
<p class="body-copy" style="left:131px;top:2348px;width:454px">Sed ut perspiciatis unde omnis iste natus error sit voluptatem accusantium doloremque laudantium, totam rem aperiam, eaque ipsa quae ab illo inventore veritatis et quasi architecto beatae vitae dicta sunt explicabo. Nemo enim ipsam voluptatem quia voluptas sit aspernatur aut odit aut fugit, sed quia consequuntur magni dolores eos qui ratione voluptatem sequi nesciunt. Neque porro quisquam est, qui dolorem ipsum quia dolor sit amet, consectetur, adipisci velit, sed quia non.</p>
<div class="btn" style="left:131px;top:2570px;width:117px;height:36px">READ MORE</div>

<svg class="abs" style="left:660px;top:2155px" width="410" height="505" viewBox="0 0 410 505">
  <defs>
    <linearGradient id="hexA" x1="0" y1="0" x2="1" y2="1"><stop offset="0" stop-color="#3c4a66"/><stop offset="1" stop-color="#8a8f99"/></linearGradient>
    <linearGradient id="hexB" x1="0" y1="0" x2="1" y2="1"><stop offset="0" stop-color="#c9c2b5"/><stop offset="1" stop-color="#7d6a55"/></linearGradient>
    <linearGradient id="hexC" x1="0" y1="0" x2="1" y2="1"><stop offset="0" stop-color="#e4e8ec"/><stop offset="1" stop-color="#5f7389"/></linearGradient>
    <linearGradient id="hexD" x1="0" y1="0" x2="1" y2="1"><stop offset="0" stop-color="#dfe3e6"/><stop offset="1" stop-color="#4a4b50"/></linearGradient>
  </defs>
  <polygon role="img" aria-label="Manager standing in a warehouse aisle" points="220,5 330,5 402,98 330,195 220,195 180,98" fill="url(#hexA)"/>
  <polygon role="img" aria-label="Happy team celebrating in an office" points="50,108 150,108 218,204 150,300 50,300 0,204" fill="url(#hexB)"/>
  <polygon role="img" aria-label="Colleagues working together at a laptop" points="220,205 330,205 402,300 330,395 220,395 180,300" fill="url(#hexC)"/>
  <polygon role="img" aria-label="Woman on a phone call at her desk" points="50,310 150,310 218,405 150,500 50,500 0,405" fill="url(#hexD)"/>
  <g font-family="Nunito, sans-serif" font-size="11" fill="#333">
    <text x="92" y="97">Heading</text>
    <text transform="translate(364 12) rotate(62)">Heading</text>
    <text transform="translate(373 395) rotate(-62)">Heading</text>
    <text transform="translate(8 448) rotate(62)">Heading</text>
  </g>
</svg>

<!-- blog -->
<h2 class="title-center" style="top:2688px">Latest Blog</h2>
<span class="rule" style="left:576px;top:2738px"></span>

<article class="card" style="left:133px">
  <div class="img" role="img" aria-label="Team cheering together seen from above" style="background:linear-gradient(135deg,#d9d9d9,#8e8e8e)"></div>
  <h3>Lorem ipsum dolor sit amet, con sectetur adipiscing elit</h3>
  <p>Sed ut perspiciatis unde omnis iste natus error sit voluptatem accusantium doloremque laudantium, totam rem aperiam, eaque ipsa quae ab illo.</p>
  <div class="btn">READ MORE</div>
</article>
<article class="card" style="left:451px">
  <div class="img" role="img" aria-label="Colleagues joining hands over a meeting table" style="background:linear-gradient(135deg,#b8c4d0,#3f4650)"></div>
  <h3>Lorem ipsum dolor sit amet, con sectetur adipiscing elit</h3>
  <p>Sed ut perspiciatis unde omnis iste natus error sit voluptatem accusantium doloremque laudantium, totam rem aperiam, eaque ipsa quae ab illo.</p>
  <div class="btn">READ MORE</div>
</article>
<article class="card" style="left:772px">
  <div class="img" role="img" aria-label="Two coworkers high-fiving by an office window" style="background:linear-gradient(135deg,#c9d3da,#2e3236)"></div>
  <h3>Lorem ipsum dolor sit amet, con sectetur adipiscing elit</h3>
  <p>Sed ut perspiciatis unde omnis iste natus error sit voluptatem accusantium doloremque laudantium, totam rem aperiam, eaque ipsa quae ab illo.</p>
  <div class="btn">READ MORE</div>
</article>

<!-- footer -->
<svg class="footer" viewBox="0 0 1200 364">
  <path d="M0 20 C400 -5 800 -5 1200 30 L1200 364 L0 364Z" fill="var(--footer)"/>
  <line x1="132" y1="280" x2="1068" y2="280" stroke="#444" stroke-width="1"/>
</svg>
<div class="foot-brand">velrato</div>

<div class="foot-h" style="left:483px">MENU</div>
<ul class="foot-menu"><li>HOME</li><li>ABOUT US</li><li>SERVICES</li><li>BLOG</li><li>CONTACT US</li></ul>

<div class="foot-h" style="left:653px">CONTACT US</div>
<span class="foot-icon" style="left:651px;top:3306px"></span>
<svg class="abs" style="left:657px;top:3311px" width="12" height="14" viewBox="0 0 12 14"><path d="M6 0 C2.5 0 0.5 2.5 0.5 5 C0.5 8.5 6 14 6 14 C6 14 11.5 8.5 11.5 5 C11.5 2.5 9.5 0 6 0Z" fill="var(--footer)"/><circle cx="6" cy="5" r="2" fill="#fff"/></svg>
<div class="foot-item" style="left:684px;top:3305px">418 Marlow Ave 3rd Floor<br>Brenton, CA 90210</div>
<span class="foot-icon" style="left:651px;top:3357px"></span>
<svg class="abs" style="left:657px;top:3363px" width="12" height="12" viewBox="0 0 12 12"><path d="M2 0 L4.5 0 L5.5 3 L4 4.5 C5 6.5 5.5 7 7.5 8 L9 6.5 L12 7.5 L12 10 C12 11 11 12 10 12 C4.5 12 0 7.5 0 2 C0 1 1 0 2 0Z" fill="var(--footer)"/></svg>
<div class="foot-item" style="left:684px;top:3355px">Call Us<br>+1 555 014 2290</div>
<span class="foot-icon" style="left:651px;top:3408px"></span>
<svg class="abs" style="left:657px;top:3416px" width="12" height="9" viewBox="0 0 12 9"><rect width="12" height="9" rx="1" fill="var(--footer)"/><path d="M0.5 0.5 L6 5 L11.5 0.5" stroke="#fff" fill="none"/></svg>
<div class="foot-item" style="left:684px;top:3406px">E mail Us<br>hello@velrato.com</div>

<div class="foot-h" style="left:965px">FOLLOW US</div>
<span class="foot-icon" style="left:963px;top:3308px"></span>
<div class="foot-item" style="left:999px;top:3306px">Like us on<br>FRIENDLY</div>
<span class="foot-icon" style="left:963px;top:3359px"></span>
<div class="foot-item" style="left:999px;top:3357px">Follow us on<br>CHIRPER</div>
<span class="foot-icon" style="left:963px;top:3410px"></span>
<div class="foot-item" style="left:999px;top:3408px">Follow us on<br>WORKLINE</div>

<div class="copyright">Copyright © 2022 All Rights Reserved</div>

</body>
</html>
```